Residential Remodeling Contractor needs updated business card

I need a new design for my business card.
Name of the company is Ridgefell Construction. I need a card that commands presence, strength, integrity. I have been in business for 28 years. I am a Residential Remodeling Contractor that covers all aspects of a residential remodel and build.

```html
<!DOCTYPE html>
<html lang="en">
<head>
<meta charset="utf-8">
<title>Ridgefell Construction – Business Card</title>
<link rel="stylesheet" href="https://fonts.googleapis.com/css2?family=Open+Sans:wght@400;600;700&display=swap">
<style>
  :root {
    --backdrop: #232323;
    --paper: #ffffff;
    --navy: #1f3a85;
    --card-blue: #213f80;
    --mark-blue: #9aaee0;
  }
  * { margin: 0; padding: 0; box-sizing: border-box; }
  html, body { width: 1200px; height: 780px; overflow: hidden; }
  body {
    background: var(--backdrop);
    font-family: "Open Sans", Arial, sans-serif;
    position: relative;
  }
  .card {
    position: absolute;
    top: 242px;
    width: 520px;
    height: 297px;
    box-shadow: 0 10px 30px rgba(0,0,0,.5);
  }
  .card--front { left: 50px; background: var(--paper); color: var(--navy); }
  .card--back  { left: 630px; background: var(--card-blue); }

  .brand {
    position: absolute;
    display: flex;
    align-items: center;
    gap: 10px;
    font-family: "Open Sans", Arial, sans-serif;
    font-weight: 600;
    text-transform: uppercase;
    letter-spacing: .06em;
    line-height: 1.15;
  }
  .brand__square { width: 18px; height: 18px; background: currentColor; flex: none; }
  .card--front .brand { left: 34px; top: 58px; font-size: 19px; color: var(--navy); }
  .card--back .brand { left: 50%; top: 50%; transform: translate(-50%, -50%); font-size: 30px; color: var(--mark-blue); gap: 16px; }
  .card--back .brand__square { width: 28px; height: 28px; }

  .divider {
    position: absolute;
    left: 244px; top: 92px;
    width: 1px; height: 130px;
    background: var(--navy);
  }
  .person { position: absolute; left: 266px; top: 94px; }
  .person__name { font-size: 27px; font-weight: 700; line-height: 1.1; }
  .person__title { font-size: 15px; font-weight: 400; margin-top: 2px; }
  .contact { list-style: none; margin-top: 12px; font-size: 13.5px; line-height: 1.45; }
  .contact li { display: flex; align-items: center; gap: 7px; }
  .contact svg { width: 11px; height: 11px; fill: var(--navy); flex: none; }
  .address {
    position: absolute; left: 34px; bottom: 26px;
    font-size: 13px;
  }
</style>
</head>
<body>
  <section class="card card--front" aria-label="Business card front">
    <div class="brand"><span class="brand__square"></span><span>Ridgefell<br>Construction</span></div>
    <div class="divider"></div>
    <div class="person">
      <h1 class="person__name">Tomas Havlen</h1>
      <p class="person__title">Managing Director</p>
      <ul class="contact">
        <li><svg viewBox="0 0 24 24"><path d="M6.6 10.8a15 15 0 0 0 6.6 6.6l2.2-2.2a1 1 0 0 1 1-.25 11.4 11.4 0 0 0 3.6.57 1 1 0 0 1 1 1V20a1 1 0 0 1-1 1A17 17 0 0 1 3 4a1 1 0 0 1 1-1h3.5a1 1 0 0 1 1 1c0 1.25.2 2.45.57 3.57a1 1 0 0 1-.25 1z"/></svg>(555) 214-0387</li>
        <li><svg viewBox="0 0 24 24"><path d="M2 5h20v14H2zm2 2v.5l8 5 8-5V7zm0 2.8V17h16V9.8l-8 5z"/></svg>hello@ridgefellbuild.com</li>
        <li><svg viewBox="0 0 24 24"><circle cx="12" cy="12" r="10"/></svg>www.ridgefellbuild.com</li>
      </ul>
    </div>
    <p class="address">1480 Alder Ridge Rd. Suite 310 Fort Worth, TX 76104</p>
  </section>

  <section class="card card--back" aria-label="Business card back">
    <div class="brand"><span class="brand__square"></span><span>Ridgefell<br>Construction</span></div>
  </section>
</body>
</html>
```